Heron Loan Partners Business Card

We need a business card design for our mortgage servicing company. In addition to servicing the loans of homeowners, we help homeowners with purchasing their homes and any mortgage refinancing. We would like to see designs that use the colors in the logo attached below (gold-ish yellow and navy blue), and any other design you deem fit! The design should communicate a simpler life with smart mortgages provided by Heron.

```html
<!DOCTYPE html>
<html lang="en">
<head>
<meta charset="utf-8">
<title>Heron Loan Partners Business Card</title>
<link href="https://fonts.googleapis.com/css2?family=Arimo:wght@400;700&display=swap" rel="stylesheet">
<style>
  :root {
    --gold: #d3a22e;
    --navy: #1d1a5c;
    --paper: #f6f6f4;
    --white: #ffffff;
    --stage: #e4e4e6;
  }
  html, body {
    margin: 0;
    width: 1200px;
    height: 874px;
    overflow: hidden;
    background: var(--stage);
    font-family: "Arimo", Arial, sans-serif;
  }
  .sheet {
    width: 1200px;
    height: 874px;
    display: flex;
    flex-direction: column;
    align-items: center;
    justify-content: center;
    gap: 40px;
  }
  .card {
    position: relative;
    width: 620px;
    height: 354px;
    border-radius: 22px;
    overflow: hidden;
    box-shadow: 0 6px 18px rgba(0,0,0,0.18);
  }
  .card-front { background: var(--gold); }
  .card-back { background: var(--paper); }

  .brand {
    position: absolute;
    left: 0; right: 0;
    display: flex;
    align-items: center;
    justify-content: center;
    gap: 14px;
    font-weight: 700;
    color: var(--navy);
  }
  .brand-dot {
    width: 18px; height: 18px;
    border-radius: 50%;
    background: var(--navy);
  }
  .card-front .brand { top: 122px; font-size: 44px; color: var(--white); }
  .card-front .brand-dot { background: var(--white); }
  .web {
    position: absolute;
    left: 0; right: 0; top: 292px;
    text-align: center;
    font-size: 15px;
    letter-spacing: 3px;
    color: #3a2e12;
  }

  .card-back .brand { top: 52px; font-size: 34px; }
  .tagline {
    position: absolute;
    left: 0; right: 0; top: 108px;
    text-align: center;
    font-size: 15px;
    color: #222;
  }
  .wave { position: absolute; inset: 0; }

  .person {
    position: absolute;
    right: 360px; top: 250px;
    text-align: right;
  }
  .person-name { font-size: 21px; font-weight: 700; color: var(--navy); }
  .person-role { font-size: 15px; color: var(--white); margin-top: 2px; }
  .divider {
    position: absolute;
    left: 282px; top: 248px;
    width: 1.5px; height: 82px;
    background: var(--white);
  }
  .contact {
    position: absolute;
    left: 300px; top: 246px;
    color: var(--white);
    font-size: 14.5px;
    line-height: 20px;
  }
  .contact-row { display: flex; align-items: center; gap: 8px; }
  .contact-row svg { width: 13px; height: 13px; flex: none; }
</style>
</head>
<body>
<main class="sheet">
  <section class="card card-front">
    <div class="brand"><span class="brand-dot"></span><span>Heron Loan Partners</span></div>
    <div class="web">www.Heron.com</div>
  </section>

  <section class="card card-back">
    <svg class="wave" viewBox="0 0 620 354" preserveAspectRatio="none" aria-hidden="true">
      <path d="M0,150 C190,215 430,185 620,250 L620,354 L0,354 Z" fill="var(--gold)"/>
      <path d="M0,156 C190,226 430,196 620,268 C430,208 190,238 0,161 Z" fill="var(--navy)"/>
    </svg>
    <div class="brand"><span class="brand-dot"></span><span>Heron Loan Partners</span></div>
    <div class="tagline">Simpler life with smart mortgages</div>

    <div class="person">
      <div class="person-name">Daniel Mercer</div>
      <div class="person-role">President</div>
    </div>
    <div class="divider"></div>
    <div class="contact">
      <div>4127 Harbor View Lane</div>
      <div>Bay Ridge, NY 11209</div>
      <div class="contact-row">
        <svg viewBox="0 0 24 24" aria-hidden="true"><path fill="#fff" d="M6.6 10.8a15 15 0 0 0 6.6 6.6l2.2-2.2c.3-.3.7-.4 1-.2 1.1.4 2.3.6 3.6.6.6 0 1 .4 1 1V20c0 .6-.4 1-1 1A17 17 0 0 1 3 4c0-.6.4-1 1-1h3.5c.6 0 1 .4 1 1 0 1.3.2 2.5.6 3.6.1.3 0 .7-.2 1z"/></svg>
        <span>(555) 0142-7788</span>
      </div>
      <div class="contact-row">
        <svg viewBox="0 0 24 24" aria-hidden="true"><path fill="#fff" d="M2 5h20v14H2z"/><path fill="none" stroke="var(--gold)" stroke-width="2" d="M2 5l10 8 10-8"/></svg>
        <span>name@Heron.com</span>
      </div>
    </div>
  </section>
</main>
</body>
</html>
```